Home Fund Guide

Have clients check their mortgage qualifications before they go looking for a mortgage lender. This program gains access to your lenders credit report / 3 scores without impacting your credit scores.

```html
<!DOCTYPE html>
<html lang="en">
<head>
<meta charset="utf-8">
<title>Home Fund Guide – Business Card</title>
<link href="https://fonts.googleapis.com/css2?family=Roboto:wght@400;500;700&display=swap" rel="stylesheet">
<style>
  :root {
    --bg: #2e2e30;
    --card: #f7f7f5;
    --blue: #1f4fc4;
    --blue-dark: #1a3fa6;
    --green: #1fc37a;
    --ink: #1c1c1c;
    --white: #ffffff;
  }
  * { box-sizing: border-box; margin: 0; padding: 0; }
  html, body { width: 1200px; height: 852px; overflow: hidden; }
  body {
    background: var(--bg);
    font-family: "Roboto", Arial, sans-serif;
    color: var(--ink);
    position: relative;
  }
  .card {
    position: absolute;
    width: 540px;
    height: 308px;
    background: var(--card);
    border-radius: 22px;
    overflow: hidden;
    top: 272px;
  }
  .card-front { left: 40px; }
  .card-back { left: 620px; }

  /* brand lockup */
  .brand { position: absolute; display: flex; align-items: center; gap: 12px; }
  .brand-mark { background: var(--blue); border-radius: 8px; }
  .brand-name { font-weight: 700; color: var(--blue); white-space: nowrap; letter-spacing: -0.5px; }

  .card-front .brand { left: 34px; top: 30px; }
  .card-front .brand-mark { width: 52px; height: 52px; }
  .card-front .brand-name { font-size: 38px; }
  .tagline {
    position: absolute; left: 98px; top: 80px;
    font-size: 10px; color: var(--blue); font-weight: 500;
  }

  .benefits {
    position: absolute; left: 40px; right: 40px; top: 108px;
    text-align: center; font-size: 14px; line-height: 1.3;
  }
  .benefits p { padding: 3px 0; }
  .benefits .rule { height: 1.5px; margin: 1px 30px; }
  .rule-green { background: var(--green); }
  .rule-blue { background: var(--blue); }

  .front-band { position: absolute; left: 0; bottom: 0; width: 540px; height: 80px; }
  .front-web {
    position: absolute; left: 0; right: 0; bottom: 40px;
    text-align: center; color: var(--white); font-size: 14px; font-weight: 500;
  }

  /* back */
  .card-back .brand { left: 40px; top: 110px; flex-direction: column; gap: 10px; width: 230px; }
  .card-back .brand-mark { width: 70px; height: 70px; border-radius: 10px; }
  .card-back .brand-name { font-size: 30px; }

  .person { position: absolute; left: 292px; top: 46px; }
  .person-name { font-size: 21px; font-weight: 700; color: var(--blue); }
  .person-title { font-size: 13px; margin-top: 2px; }
  .contacts { list-style: none; margin-top: 12px; font-size: 13px; line-height: 1.35; }
  .contacts li { display: flex; align-items: flex-start; gap: 8px; }
  .contacts svg { width: 13px; height: 13px; flex: none; margin-top: 2px; }
  .contacts .address { margin-top: 8px; padding-left: 21px; }

  .back-sweep { position: absolute; left: 0; bottom: 0; width: 540px; height: 70px; }
  .credential {
    position: absolute; right: 0; bottom: 24px;
    width: 250px; height: 42px;
    background: var(--blue);
    border-radius: 16px 0 0 0;
    color: var(--white); font-size: 13px;
    display: flex; align-items: center; justify-content: center;
  }
</style>
</head>
<body>

<section class="card card-front">
  <div class="brand">
    <span class="brand-mark"></span>
    <span class="brand-name">Home Fund Guide</span>
  </div>
  <p class="tagline">is Managed by Keystone Financial, A 401(c)(3) Nonprofit Certified Credit Counselor</p>

  <div class="benefits">
    <p>Discover Your Mortgage Qualifications - FHA, Conv., VA, USDA</p>
    <div class="rule rule-green"></div>
    <p>Find Out Your Lender's 3 CreditMark® (Classic) Scores</p>
    <div class="rule rule-blue"></div>
    <p>Your Credit Report will be Analyzed for Score Improvement</p>
    <div class="rule rule-green"></div>
    <p>HFG will Identify Your Personal Steps to Higher CreditMark Scores<br>(66 Average Point Improvement)</p>
  </div>

  <svg class="front-band" viewBox="0 0 540 80" preserveAspectRatio="none">
    <defs>
      <linearGradient id="bandFade" x1="0" y1="0" x2="1" y2="0">
        <stop offset="0" stop-color="#1f4fc4" stop-opacity="0.9"/>
        <stop offset="1" stop-color="#1fc37a"/>
      </linearGradient>
    </defs>
    <path d="M0 14 H540 V80 H0 Z" fill="url(#bandFade)"/>
    <path d="M0 50 H190 L220 80 H0 Z" fill="#1f4fc4"/>
  </svg>
  <p class="front-web">www.HomeFundGuide.org</p>
</section>

<section class="card card-back">
  <div class="brand">
    <span class="brand-mark"></span>
    <span class="brand-name">Home Fund Guide</span>
  </div>

  <div class="person">
    <h1 class="person-name">Dana Wells</h1>
    <p class="person-title">Managing Director</p>
    <ul class="contacts">
      <li>
        <svg viewBox="0 0 16 16"><path d="M3 2h3l1.5 3.5-2 1.3a8 8 0 0 0 3.7 3.7l1.3-2L14 10v3a1 1 0 0 1-1 1A11 11 0 0 1 2 3a1 1 0 0 1 1-1z" fill="#1f4fc4"/></svg>
        <span>(877) 555-0142</span>
      </li>
      <li>
        <svg viewBox="0 0 16 16"><rect x="1" y="3" width="14" height="10" rx="1" fill="#1fc37a"/><path d="M1.5 4 8 9l6.5-5" stroke="#fff" stroke-width="1.3" fill="none"/></svg>
        <span>Support@HomeFundGuide.org</span>
      </li>
      <li>
        <svg viewBox="0 0 16 16"><circle cx="8" cy="8" r="6.5" fill="none" stroke="#1f4fc4" stroke-width="1.4"/><ellipse cx="8" cy="8" rx="2.8" ry="6.5" fill="none" stroke="#1f4fc4" stroke-width="1.2"/><path d="M1.5 8h13" stroke="#1f4fc4" stroke-width="1.2"/></svg>
        <span>www.HomeFundGuide.org</span>
      </li>
      <li class="address">318 Harbor Lane, Suite 210,<br>Lakeview, Oregon 97630</li>
    </ul>
  </div>

  <svg class="back-sweep" viewBox="0 0 540 70" preserveAspectRatio="none">
    <path d="M0 56 Q200 54 300 24 L320 24 Q250 62 0 70 Z" fill="#1fc37a"/>
    <path d="M0 64 H540 V70 H0 Z" fill="#1fc37a"/>
  </svg>
  <div class="credential">As a Certified Credit Counselor</div>
</section>

</body>
</html>
```